High Tech Real Estate Startup needs a business card

We are developing an innovative real estate marketing product based around advanced search and virtual reality.

We talk to people, we need business cards.

Target Market(s)

The target market is technology professionals and realtors.

Contact Information for Business Card

The information to be included will include

Name
Title
Phone Number
E-mail Address
www.zelquin.com

It should use simple iconography for each one of those fields.

Font styles to use
Other font styles liked:
• Co, Jubilat, Avenir

Colors

Designer to choose colors to be used in the design.

Requirements
Must have
• Clean aesthetic,
• Good use of negative space.
• It should use our company logo, shown in the attached file. It is able to use the negative of that logo (coloured font and white background) and I have attached other acceptable accent colours in a swatch file.
Should not have
• Should not be too busy
• No extraneous text (slogans, tag lines etc)

```html
<!DOCTYPE html>
<html lang="en">
<head>
<meta charset="utf-8">
<title>Zelquin Business Card</title>
<link rel="stylesheet" href="https://fonts.googleapis.com/css2?family=Nunito+Sans:wght@400;600&display=swap">
<style>
  :root {
    --teal: #08b9c0;
    --ink: #5b6a70;
    --paper: #ffffff;
    --backdrop: #e4e5e6;
  }
  * { margin: 0; padding: 0; box-sizing: border-box; }
  html, body {
    width: 1200px;
    height: 1000px;
    overflow: hidden;
    background: var(--backdrop);
    font-family: "Nunito Sans", "Avenir", sans-serif;
  }
  .canvas { position: relative; width: 1200px; height: 1000px; }

  .card {
    position: absolute;
    background: var(--paper);
    border-radius: 40px;
    overflow: hidden;
  }
  .card--front { left: 152px; top: 102px; width: 626px; height: 358px; }
  .card--back  { left: 370px; top: 545px; width: 635px; height: 362px; }

  .wordmark {
    position: absolute;
    font-weight: 600;
    letter-spacing: 2px;
    line-height: 1;
    white-space: nowrap;
  }
  .card--front .wordmark {
    color: var(--teal);
    font-size: 88px;
    left: 50%;
    top: 50%;
    transform: translate(-50%, -52%);
  }

  .card__wave { position: absolute; inset: 0; width: 635px; height: 362px; }
  .card--back .wordmark {
    color: var(--paper);
    font-size: 38px;
    right: 30px;
    top: 160px;
  }

  .person { position: absolute; left: 34px; top: 122px; color: var(--ink); }
  .person__name { font-size: 32px; font-weight: 400; line-height: 1; }
  .person__title { font-size: 17px; margin-top: 12px; line-height: 1; }
  .person__rule {
    position: absolute;
    left: 188px;
    top: 177px;
    width: 194px;
    height: 2px;
    background: var(--ink);
  }

  .contacts { position: absolute; left: 36px; top: 232px; list-style: none; }
  .contacts li {
    display: flex;
    align-items: center;
    height: 29.5px;
    font-size: 21px;
    letter-spacing: 1.6px;
    color: var(--ink);
  }
  .contacts svg { width: 18px; height: 18px; margin-right: 23px; fill: var(--ink); }
</style>
</head>
<body>
<main class="canvas">
  <section class="card card--front">
    <span class="wordmark">ZELQUIN</span>
  </section>

  <section class="card card--back">
    <svg class="card__wave" viewBox="0 0 635 362" aria-hidden="true">
      <path fill="var(--teal)" d="M355,0 C340,70 400,120 420,190 C440,260 445,310 418,362 L635,362 L635,0 Z"/>
    </svg>
    <span class="wordmark">ZELQUIN</span>

    <div class="person">
      <p class="person__name">Name of Person</p>
      <p class="person__title">Title of Person</p>
    </div>
    <span class="person__rule"></span>

    <ul class="contacts">
      <li>
        <svg viewBox="0 0 24 24" aria-hidden="true"><path d="M6.6 10.8a15.1 15.1 0 0 0 6.6 6.6l2.2-2.2a1 1 0 0 1 1-.25 11.4 11.4 0 0 0 3.6.57 1 1 0 0 1 1 1V20a1 1 0 0 1-1 1A17 17 0 0 1 3 4a1 1 0 0 1 1-1h3.5a1 1 0 0 1 1 1c0 1.25.2 2.45.57 3.57a1 1 0 0 1-.25 1z"/></svg>
        +123 456 7890
      </li>
      <li>
        <svg viewBox="0 0 24 24" aria-hidden="true"><path d="M12 2a10 10 0 1 0 0 20 10 10 0 0 0 0-20zm6.9 6h-2.9a15.7 15.7 0 0 0-1.4-3.6A8 8 0 0 1 18.9 8zM12 4c.8 1.2 1.5 2.5 1.9 4h-3.8c.4-1.5 1.1-2.8 1.9-4zM4.3 14a8.2 8.2 0 0 1 0-4h3.4a16.5 16.5 0 0 0 0 4zm.8 2h2.9c.3 1.3.8 2.5 1.4 3.6A8 8 0 0 1 5.1 16zM8 8H5.1a8 8 0 0 1 4.3-3.6C8.8 5.5 8.3 6.7 8 8zm4 12c-.8-1.2-1.5-2.5-1.9-4h3.8c-.4 1.5-1.1 2.8-1.9 4zm2.3-6H9.7a14.7 14.7 0 0 1 0-4h4.6a14.7 14.7 0 0 1 0 4zm.3 5.6c.6-1.1 1.1-2.3 1.4-3.6h2.9a8 8 0 0 1-4.3 3.6zm1.7-5.6a16.5 16.5 0 0 0 0-4h3.4a8.2 8.2 0 0 1 0 4z"/></svg>
        www.zelquin.com
      </li>
      <li>
        <svg viewBox="0 0 24 24" aria-hidden="true"><path d="M2 5h20v2.2l-10 6-10-6z M2 9.5l10 6 10-6V19H2z"/></svg>
        E-mail Address
      </li>
    </ul>
  </section>
</main>
</body>
</html>
```